Heron Loan Partners Business Card

We need a business card design for our mortgage servicing company. In addition to servicing the loans of homeowners, we help homeowners with purchasing their homes and any mortgage refinancing. We would like to see designs that use the colors in the logo attached below (gold-ish yellow and navy blue), and any other design you deem fit! The design should communicate a simpler life with smart mortgages provided by Heron.

```html
<!DOCTYPE html>
<html lang="en">
<head>
<meta charset="utf-8">
<title>Heron Loan Partners Business Card</title>
<link href="https://fonts.googleapis.com/css2?family=Open+Sans:wght@400;600;700&display=swap" rel="stylesheet">
<style>
  :root {
    --stage: #232323;
    --gold: #e0b23d;
    --navy: #2b2a63;
    --paper: #ffffff;
    --ink: #1e1e1e;
  }
  * { margin: 0; padding: 0; box-sizing: border-box; }
  html, body { width: 1200px; height: 780px; overflow: hidden; }
  body {
    background: var(--stage);
    font-family: "Open Sans", Arial, sans-serif;
    display: flex;
    align-items: center;
    justify-content: center;
    gap: 40px;
  }
  .card {
    width: 560px;
    height: 320px;
    position: relative;
    box-shadow: 0 12px 30px rgba(0,0,0,.45);
  }
  .card-front {
    background: var(--gold);
    display: flex;
    align-items: center;
    justify-content: center;
    gap: 14px;
  }
  .brand-dot {
    width: 22px; height: 22px;
    border-radius: 50%;
    background: var(--navy);
  }
  .brand-name {
    font-weight: 700;
    font-size: 38px;
    color: var(--navy);
    letter-spacing: .5px;
  }
  .card-back {
    background: var(--paper);
    padding: 0 36px;
  }
  .identity-row {
    position: absolute;
    top: 92px; left: 36px; right: 30px;
    display: flex;
    align-items: center;
  }
  .identity { flex: 0 0 auto; }
  .person-name {
    font-size: 30px;
    font-weight: 700;
    line-height: 1.1;
  }
  .person-name .first { color: var(--gold); }
  .person-name .last { color: var(--navy); }
  .person-title {
    font-size: 15px;
    font-weight: 600;
    color: var(--ink);
    margin-left: 90px;
    letter-spacing: .6px;
  }
  .divider {
    width: 1.5px;
    height: 92px;
    background: var(--navy);
    margin: 0 24px;
  }
  .contact-list { list-style: none; }
  .contact-item {
    display: flex;
    align-items: center;
    gap: 10px;
    font-size: 15px;
    color: var(--ink);
    letter-spacing: .5px;
    line-height: 1.55;
  }
  .contact-icon { width: 13px; height: 13px; flex: 0 0 13px; }
  .address {
    position: absolute;
    left: 0; right: 0; bottom: 58px;
    text-align: center;
    font-size: 15px;
    color: var(--ink);
    letter-spacing: .6px;
  }
</style>
</head>
<body>
  <section class="card card-front" aria-label="Card front">
    <span class="brand-dot"></span>
    <span class="brand-name">Heron Loan Partners</span>
  </section>

  <section class="card card-back" aria-label="Card back">
    <div class="identity-row">
      <div class="identity">
        <p class="person-name"><span class="first">Lenka</span> <span class="last">Horvath</span></p>
        <p class="person-title">Managing Director</p>
      </div>
      <span class="divider"></span>
      <ul class="contact-list">
        <li class="contact-item">
          <svg class="contact-icon" viewBox="0 0 16 16"><path fill="#e0b23d" d="M3.5 1l2.5 3-1.5 2c1 2 3 4 5 5l2-1.5 3 2.5-1.5 2.5C8 16 0 8 1 2.5z"/></svg>
          (555) 014-2290
        </li>
        <li class="contact-item">
          <svg class="contact-icon" viewBox="0 0 16 16"><rect x="1" y="3" width="14" height="10" rx="1.5" fill="#e0b23d"/><path d="M1.5 4l6.5 5 6.5-5" stroke="#fff" stroke-width="1.4" fill="none"/></svg>
          info@heronloans.com
        </li>
        <li class="contact-item">
          <svg class="contact-icon" viewBox="0 0 16 16"><circle cx="8" cy="8" r="7" fill="#e0b23d"/><path d="M1 8h14M8 1c-3 3-3 11 0 14M8 1c3 3 3 11 0 14" stroke="#fff" stroke-width="1" fill="none"/></svg>
          www.heronloans.com
        </li>
      </ul>
    </div>
    <p class="address">1840 Lakeside Ave. Suite 210 Riverton, TX 75001</p>
  </section>
</body>
</html>
```